Corvane Business Cards

Front of business card will have logo, name, address, & telephone number. Back of card will have a list of services provided - Roads, Substation Pads, Temporary Pads, Site Pads, Land Leveling, Powerline Row Cleaning, Land Clearing, Gates, Fencing, Construction Entrances, Excavation, Trenching, Underground Utilities, Directional Boring, Pile Driving. We are a construction company that uses heavy equipment like bulldozers, motor graders/blades, dump trucks, backhoes, hydro axes, & skid loaders. We build roads, pads, & install electric utility lines & waterlines underground. This logo is new. The word "Construction" can be smaller as uploaded 2 example edited logos. We will be using this card design for many employees.
Target Market(s)
Industrial Electric Powerline, Wind Turbine, Solar Panel, & Water Utility companies.
Contact Information for Business Card
Name/Position - Dwayne Halster - Owner
Address: 4875 FM 309
Harlow Springs, NM 88214
Phone number - (575) 482-5096

```html
<!DOCTYPE html>
<html lang="en">
<head>
<meta charset="utf-8">
<title>Corvane Construction Business Cards</title>
<link rel="stylesheet" href="https://fonts.googleapis.com/css2?family=Montserrat:wght@400;500;600;700&display=swap">
<style>
  :root {
    --bg: #1d1d1f;
    --card: #430f1c;
    --card-deep: #380b17;
    --ink: #ffffff;
    --ink-soft: #f1e6e8;
  }
  * { margin: 0; padding: 0; box-sizing: border-box; }
  html, body {
    width: 1200px; height: 852px; overflow: hidden;
    background: var(--bg);
    font-family: "Montserrat", Arial, sans-serif;
    color: var(--ink);
  }
  .stage {
    position: relative; width: 1200px; height: 852px;
    display: flex; align-items: center; justify-content: center; gap: 34px;
  }
  .card {
    position: relative; width: 560px; height: 320px;
    border-radius: 18px;
    background: linear-gradient(160deg, var(--card) 0%, var(--card-deep) 100%);
    overflow: hidden;
  }
  .brand {
    display: flex; flex-direction: column; align-items: center;
    font-weight: 600; letter-spacing: 2px; line-height: 1;
  }
  .brand-name { font-size: 26px; }
  .brand-sub { font-size: 36px; margin-top: 6px; }

  /* services side */
  .card--services .brand { position: absolute; top: 40px; left: 0; right: 0; }
  .services {
    position: absolute; left: 34px; bottom: 30px;
    display: flex; align-items: flex-end; gap: 26px;
    font-size: 13.5px; font-weight: 500; color: var(--ink-soft);
  }
  .services-col { list-style: none; }
  .services-col li { position: relative; padding-left: 13px; line-height: 1.55; white-space: nowrap; }
  .services-col li::before {
    content: ""; position: absolute; left: 0; top: 8px;
    width: 5px; height: 5px; border-radius: 50%; background: var(--ink);
  }
  .services-col--second { margin-bottom: 22px; }
  .services-col--third { margin-bottom: 46px; }
  .services-title { font-weight: 700; font-size: 14.5px; margin-bottom: 2px; }

  /* contact side */
  .card--contact { display: flex; flex-direction: column; align-items: center; padding-top: 46px; }
  .card--contact .brand-name { font-size: 22px; }
  .card--contact .brand-sub { font-size: 30px; }
  .rule { width: 300px; height: 1.5px; background: var(--ink); margin: 14px 0; }
  .person-name { font-weight: 700; font-size: 19px; letter-spacing: 1px; }
  .person-role { font-size: 14px; margin-top: 2px; }
  .contact-line { font-size: 16px; line-height: 1.6; text-align: center; letter-spacing: 0.5px; white-space: nowrap; }
</style>
</head>
<body>
<main class="stage">
  <section class="card card--services">
    <div class="brand">
      <span class="brand-name">CORVANE</span>
      <span class="brand-sub">CONSTRUCTION</span>
    </div>
    <div class="services">
      <div>
        <p class="services-title">Services:</p>
        <ul class="services-col services-col--first">
          <li>Roads</li><li>Site Pads</li><li>Gates</li><li>Fencing</li>
        </ul>
      </div>
      <ul class="services-col services-col--second">
        <li>Trenching</li><li>Temporary Pads</li><li>Land Leveling</li><li>Land Clearing</li><li>Substation Pads</li>
      </ul>
      <ul class="services-col services-col--third">
        <li>Powerline Row Cleaning</li><li>Construction Entrances</li><li>Excavation</li><li>Underground Utilities</li><li>Directional Boring, Pile Driving</li>
      </ul>
    </div>
  </section>

  <section class="card card--contact">
    <div class="brand">
      <span class="brand-name">CORVANE</span>
      <span class="brand-sub">CONSTRUCTION</span>
    </div>
    <div class="rule"></div>
    <p class="person-name">DWAYNE HALSTER</p>
    <p class="person-role">owner</p>
    <div class="rule"></div>
    <p class="contact-line">(575) 482-5096</p>
    <p class="contact-line">4875 FM 309 Harlow Springs, NM 88214</p>
  </section>
</main>
</body>
</html>
```